Diverse, up-scale salon needs eye-catching, unique business cards.

We are looking for a unique business card design for our stylist but that can also be multi functional and used for appointment reminder and referrals. I will need a design in a format that I can modify names and titles going forward. In the past we have had a dark background with the logo on one side, and stylist and contact information on the other but we are open to all ideas. I have included our mission statement as well as branded colors below. The statement doesn't need to go on the card, it's just a reference for target market. We need space for the stylists name, title, instagram handle and then the salons phone number, website and address. I am also open to adding a spot for a qr code linked to the stylist instagram or the salon booking link.

primary brand colors:
#333333 #233415 #36502a #93874a #000000
Mission statement:
Vessolin Hair Studio, a high-end salon located in the lively Downtown Farmington, Michigan, is committed to providing exceptional services in a welcoming and relaxed environment to meet the needs of our diverse clientele.
Our salon specializes in contemporary custom haircuts, coloring, extensions, and barbering and beard grooming services. Our team of skilled stylists is passionate and inventive in their hair styling techniques. At the heart of our salon are values centered on quality, innovation, creativity, and above all, comfort. These core values are evident in every appointment across our customizable array of services.
Our goal is to establish a benchmark for exceptional hair care for every human.
Website: www.vessolinhairstudio.example
instagram: @vessolinhairstudio
address: 41782 Pelham Crest Rd, Farmington MI
phone: 248-613-4087

Industry/Entity Type

Hair Salon

Contact Information for Business Card

Stylist name, title, phone, instagram, website, address, (optional qr code)

Requirements
Should not have
• Does not need mission statement on the card.

```html
<!DOCTYPE html>
<html lang="en">
<head>
<meta charset="utf-8">
<title>Vessolin Hair Studio – Business Card</title>
<link rel="stylesheet" href="https://fonts.googleapis.com/css2?family=Cinzel:wght@500&family=Montserrat:wght@400;600&display=swap">
<style>
  :root {
    --stage: #3b3b3b;
    --card: #151515;
    --gold: #93874a;
    --white: #f2f2f2;
    --muted: #cfcfcf;
  }
  * { box-sizing: border-box; margin: 0; padding: 0; }
  html, body { width: 1200px; height: 801px; overflow: hidden; }
  body {
    background: var(--stage);
    font-family: "Montserrat", sans-serif;
    position: relative;
  }
  .card {
    position: absolute;
    top: 252px;
    width: 520px;
    height: 297px;
    background: var(--card);
    border: 1.5px solid var(--gold);
    box-shadow: 0 14px 30px rgba(0,0,0,.35);
    overflow: hidden;
  }
  .card--front { left: 50px; }
  .card--back { left: 630px; }

  /* brand mark stand-in */
  .brand {
    position: absolute;
    display: flex;
    align-items: center;
    gap: 12px;
    color: var(--gold);
    font-weight: 600;
    letter-spacing: 2px;
    text-transform: uppercase;
    line-height: 1.25;
  }
  .brand__dot {
    flex: none;
    border: 2px solid var(--gold);
    border-radius: 50%;
  }
  .card--front .brand { left: 32px; top: 36px; font-size: 13px; }
  .card--front .brand__dot { width: 58px; height: 58px; }
  .card--back .brand { right: 40px; top: 96px; font-size: 16px; }
  .card--back .brand__dot { width: 92px; height: 92px; }

  /* stylist */
  .stylist {
    position: absolute;
    right: 34px;
    top: 34px;
    text-align: right;
  }
  .stylist__name {
    font-family: "Cinzel", serif;
    font-weight: 500;
    color: var(--gold);
    font-size: 24px;
    letter-spacing: 1px;
    line-height: 1;
  }
  .stylist__title {
    color: var(--white);
    font-size: 12px;
    margin-top: 4px;
  }
  .stylist__rule {
    width: 118px;
    height: 1px;
    background: var(--gold);
    margin: 8px 0 0 auto;
  }
  .address {
    position: absolute;
    right: 34px;
    top: 118px;
    text-align: right;
    color: var(--white);
    font-size: 12px;
    line-height: 1.5;
  }
  .divider {
    position: absolute;
    left: 28px;
    right: 28px;
    top: 176px;
    height: 1px;
    background: var(--gold);
  }
  .contact {
    position: absolute;
    left: 32px;
    top: 196px;
    list-style: none;
    color: var(--white);
    font-size: 12.5px;
    line-height: 1;
  }
  .contact li {
    display: flex;
    align-items: center;
    gap: 8px;
    margin-bottom: 10px;
  }
  .contact__icon { width: 12px; height: 12px; flex: none; }
</style>
</head>
<body>

  <section class="card card--front" aria-label="Card front">
    <div class="brand">
      <span class="brand__dot"></span>
      <span>Vessolin<br>Hair Studio</span>
    </div>

    <div class="stylist">
      <p class="stylist__name">MARISOL</p>
      <p class="stylist__title">President</p>
      <div class="stylist__rule"></div>
    </div>

    <p class="address">41782 Pelham Crest Rd<br>Farmington MI</p>

    <div class="divider"></div>

    <ul class="contact">
      <li>
        <svg class="contact__icon" viewBox="0 0 24 24" aria-hidden="true">
          <path fill="#cfcfcf" d="M6.6 10.8a15.1 15.1 0 0 0 6.6 6.6l2.2-2.2a1 1 0 0 1 1-.25 11.4 11.4 0 0 0 3.6.57 1 1 0 0 1 1 1V20a1 1 0 0 1-1 1A17 17 0 0 1 3 4a1 1 0 0 1 1-1h3.5a1 1 0 0 1 1 1c0 1.25.2 2.45.57 3.57a1 1 0 0 1-.25 1z"/>
        </svg>
        248-613-4087
      </li>
      <li>
        <svg class="contact__icon" viewBox="0 0 24 24" aria-hidden="true">
          <circle cx="12" cy="12" r="9" fill="none" stroke="#cfcfcf" stroke-width="3"/>
        </svg>
        @vessolinhairstudio
      </li>
      <li>
        <svg class="contact__icon" viewBox="0 0 24 24" aria-hidden="true">
          <circle cx="12" cy="12" r="9" fill="none" stroke="#cfcfcf" stroke-width="2"/>
          <path d="M3 12h18M12 3c3 3 3 15 0 18M12 3c-3 3-3 15 0 18" fill="none" stroke="#cfcfcf" stroke-width="1.6"/>
        </svg>
        www.vessolinhairstudio.example
      </li>
    </ul>
  </section>

  <section class="card card--back" aria-label="Card back">
    <div class="brand">
      <span class="brand__dot"></span>
      <span>Vessolin<br>Hair Studio</span>
    </div>
  </section>

</body>
</html>
```